Zenqo - revolutionary mobile payment

The app is a P2P money trasfert, without the using of credit card or bank circuits it can transfer electronic money from one person to another consumers simply and immediatelly.
You can use the color you want, but the message we need to transert to consumer is simplicity, safety and coolness.
In attach the logo of the company and the wireframe of thre page of the app.
The goal is to design the page of the app with a clear, simple and intuitive graphic.
Updates

I have upgrade the brief with important information and detail, many thanks

Target Market(s)

all the people

Industry/Entity Type

Credit Card

Requirements
Must have
• You have to design one icon for each button in the first page, (shop is: where to shop)
in the second one a new intuitive image (instead of the hand) that let the user to understand that with a simple swipe he can process the payment
Nice to have
• You can include or esxclude what you want or belive can improve user experience of the app
Should not have
• too much color, too much button or information

```html
<!DOCTYPE html>
<html lang="en">
<head>
<meta charset="utf-8">
<title>Zenqo – Home</title>
<link rel="stylesheet" href="https://fonts.googleapis.com/css2?family=Mulish:wght@400;600;800&display=swap">
<style>
  :root{
    --page-bg:#c3c6ca;
    --status-bg:#0c0c0c;
    --nav-top:#ffffff;
    --nav-bottom:#d9d9d9;
    --brand-navy:#22418a;
    --backdrop-dark:#3a3736;
    --backdrop-mid:#5b5553;
    --accent-orange:#e3701c;
    --tile-bg:rgba(38,35,34,.88);
    --profile-band:rgba(30,28,28,.78);
    --ink-light:#ffffff;
    --ink-muted:#d6d6d6;
    --icon-dark:#3a3a3a;
  }
  *{box-sizing:border-box;margin:0;padding:0}
  html,body{width:1200px;height:1195px;overflow:hidden}
  body{background:var(--page-bg);font-family:"Mulish",sans-serif;position:relative}

  .app-screen{
    position:absolute;left:290px;top:47px;width:620px;height:1100px;
    overflow:hidden;background:var(--backdrop-dark);
    box-shadow:0 20px 50px rgba(0,0,0,.25);
  }

  .status-bar{
    position:absolute;left:0;top:0;width:100%;height:40px;background:var(--status-bg);
    color:var(--ink-light);font-size:21px;font-weight:600;
    display:flex;align-items:center;justify-content:space-between;padding:0 14px;
  }
  .status-bar .carrier{display:flex;align-items:center;gap:8px}
  .status-bar .signal{display:flex;gap:3px}
  .status-bar .signal i{width:9px;height:9px;border-radius:50%;background:var(--ink-light)}
  .status-bar .signal i.off{background:none;border:1.5px solid var(--ink-light)}
  .status-bar .time{position:absolute;left:50%;transform:translateX(-50%)}
  .status-bar .power{display:flex;align-items:center;gap:8px}
  .battery{width:40px;height:18px;border:2px solid var(--ink-light);border-radius:3px;position:relative;padding:2px}
  .battery::after{content:"";position:absolute;right:-6px;top:4px;width:3px;height:7px;background:var(--ink-light)}
  .battery span{display:block;width:22%;height:100%;background:var(--ink-light)}

  .nav-bar{
    position:absolute;left:0;top:40px;width:100%;height:84px;
    background:linear-gradient(var(--nav-top),var(--nav-bottom));
    display:flex;align-items:center;justify-content:space-between;padding:0 22px;
  }
  .brand{display:flex;align-items:center;gap:10px;color:var(--brand-navy);font-size:34px;font-weight:800}
  .brand .mark{width:30px;height:30px;border-radius:50%;background:var(--brand-navy)}

  .backdrop{
    position:absolute;left:0;top:124px;width:100%;height:976px;
    background:
      radial-gradient(ellipse 160px 120px at 270px 220px, rgba(235,120,30,.95), transparent 70%),
      radial-gradient(ellipse 200px 140px at 120px 420px, rgba(220,105,25,.85), transparent 70%),
      radial-gradient(ellipse 180px 200px at 380px 560px, rgba(200,95,20,.8), transparent 70%),
      radial-gradient(ellipse 200px 160px at 500px 180px, rgba(240,240,240,.7), transparent 70%),
      radial-gradient(ellipse 220px 260px at 520px 700px, rgba(120,110,105,.7), transparent 70%),
      radial-gradient(ellipse 180px 200px at 120px 860px, rgba(180,90,30,.7), transparent 70%),
      linear-gradient(160deg,var(--backdrop-mid),var(--backdrop-dark) 60%,#262322);
  }

  .profile-band{
    position:absolute;left:0;top:124px;width:100%;height:250px;
    background:linear-gradient(var(--profile-band),rgba(30,28,28,.55));
  }
  .edit-button{
    position:absolute;right:26px;top:144px;width:44px;height:44px;border-radius:50%;
    background:#e6e6e6;display:flex;align-items:center;justify-content:center;
  }
  .avatar{
    position:absolute;left:30px;top:242px;width:104px;height:104px;border-radius:50%;
    border:5px solid var(--ink-light);
    background:radial-gradient(circle at 50% 40%,#c9a58c,#6f7d5a 70%);
  }
  .profile-text{position:absolute;left:170px;top:232px;color:var(--ink-light)}
  .profile-text .name{font-size:38px;font-weight:800;letter-spacing:.3px}
  .profile-text .phone{font-size:20px;color:var(--ink-muted);margin-top:2px;letter-spacing:1px}

  .action-grid{
    position:absolute;left:44px;top:420px;width:532px;
    display:grid;grid-template-columns:256px 256px;gap:20px;
  }
  .action-tile{
    height:250px;background:var(--tile-bg);border-radius:6px;
    display:flex;flex-direction:column;align-items:center;justify-content:center;gap:14px;
    color:var(--ink-light);font-size:30px;font-weight:800;
  }
  .action-tile svg{width:130px;height:120px}
</style>
</head>
<body>
  <main class="app-screen">
    <div class="backdrop" role="img" aria-label="Blurred photographic backdrop in grey and warm orange tones"></div>

    <header class="status-bar">
      <div class="carrier">
        <span class="signal"><i></i><i></i><i></i><i class="off"></i><i class="off"></i></span>
        <span>NOVA</span>
        <svg width="22" height="16" viewBox="0 0 22 16" aria-hidden="true"><path d="M1 6a15 15 0 0 1 20 0M4.5 9.5a10 10 0 0 1 13 0M8 13a5 5 0 0 1 6 0" stroke="#fff" stroke-width="2.2" fill="none"/></svg>
      </div>
      <span class="time">4:21 PM</span>
      <div class="power"><span>22%</span><span class="battery"><span></span></span></div>
    </header>

    <nav class="nav-bar">
      <svg class="settings" width="44" height="40" viewBox="0 0 44 40" aria-label="Settings">
        <g fill="#333">
          <circle cx="17" cy="22" r="10"/>
          <g stroke="#333" stroke-width="5">
            <path d="M17 8v28M3 22h28M7 12l20 20M27 12L7 32"/>
          </g>
          <circle cx="35" cy="10" r="6"/>
          <g stroke="#333" stroke-width="3"><path d="M35 1v18M26 10h18"/></g>
        </g>
        <circle cx="17" cy="22" r="4" fill="#eee"/>
        <circle cx="35" cy="10" r="2.5" fill="#eee"/>
      </svg>
      <div class="brand"><span class="mark"></span>Zenqo</div>
    </nav>

    <section class="profile-band"></section>
    <div class="edit-button" aria-label="Edit profile">
      <svg width="22" height="22" viewBox="0 0 22 22"><path d="M4 18l2-6L15 3l4 4-9 9z" fill="#333"/><path d="M3 20h8" stroke="#333" stroke-width="2"/></svg>
    </div>
    <div class="avatar" role="img" aria-label="Profile photo of the account holder"></div>
    <div class="profile-text">
      <p class="name">Marco Ellery</p>
      <p class="phone">+39 312 555 0147</p>
    </div>

    <section class="action-grid">
      <a class="action-tile">
        <svg viewBox="0 0 130 120" aria-hidden="true">
          <rect x="44" y="38" width="80" height="58" rx="5" fill="#fff"/>
          <rect x="44" y="78" width="80" height="8" fill="#555"/>
          <text x="104" y="64" font-family="Mulish,sans-serif" font-weight="800" font-size="22" fill="#333" text-anchor="middle">€</text>
          <path d="M4 30h44c10 0 16 6 16 12s-6 10-14 10H34c4 6 12 8 22 8v12H30C14 72 4 60 4 46z" fill="#fff"/>
        </svg>
        Pay
      </a>
      <a class="action-tile">
        <svg viewBox="0 0 130 120" aria-hidden="true">
          <rect x="54" y="30" width="72" height="56" rx="5" fill="#fff"/>
          <text x="108" y="62" font-family="Mulish,sans-serif" font-weight="800" font-size="22" fill="#333" text-anchor="middle">€</text>
          <path d="M6 50l40 30 40-30v46H6z" fill="#fff" stroke="#3a3a3a" stroke-width="3"/>
          <path d="M30 8h22v26h14L41 60 16 34h14z" fill="#fff" stroke="#3a3a3a" stroke-width="3"/>
          <g stroke="#555" stroke-width="3"><path d="M54 86h60M60 92h50"/></g>
        </svg>
        Ask
      </a>
      <a class="action-tile">
        <svg viewBox="0 0 130 120" aria-hidden="true">
          <circle cx="52" cy="26" r="22" fill="#fff"/>
          <path d="M14 112V72c0-12 8-20 20-20h36c12 0 20 8 20 20v40z" fill="#fff"/>
          <path d="M40 52l12 14 12-14" fill="#3a3a3a"/>
          <path d="M49 66h6l4 30-7 8-7-8z" fill="#3a3a3a"/>
          <rect x="68" y="80" width="16" height="4" fill="#3a3a3a"/>
        </svg>
        Account
      </a>
      <a class="action-tile">
        <svg viewBox="0 0 130 120" aria-hidden="true">
          <path d="M42 18L26 50M88 18l16 32" stroke="#fff" stroke-width="7" stroke-linecap="round"/>
          <rect x="6" y="48" width="118" height="14" rx="3" fill="#fff"/>
          <path d="M14 66h102l-12 44H26z" fill="#fff"/>
          <g fill="#3a3a3a">
            <rect x="36" y="74" width="7" height="28" rx="3"/>
            <rect x="52" y="74" width="7" height="28" rx="3"/>
            <rect x="68" y="74" width="7" height="28" rx="3"/>
            <rect x="84" y="74" width="7" height="28" rx="3"/>
          </g>
        </svg>
        Shop
      </a>
    </section>
  </main>
</body>
</html>
```